Lotstallmart.com Webpage Design

Design Brief for lotstallmart.com (Copy of Brief also in attached Word file)

Name of Website- lotstallmart.com (existing logo and look & feel of website to be changed)

Logo - Finalised. The logo files are attached with the brief as “logo.jpeg”. The “Blue- Grey” version of the logo is for use on lighter backgrounds and the “Orange-White” version of the logo is for use on darker backgrounds. (A full Black version of the logo is also attached). Both versions may be used in different parts of the website. All attached files are in .png format.
Status - The website in functional and is undergoing user trials. However, we want to improve the look & feel of the website so at it seems
a. cotemporary,
b. Easy to Navigate
c. professional and
d. Vibrant.

Please visit ‘lotstallmart.com’ to check out the website and its functionalities – please use it only as a reference for the features & functions to be provided, however the designer should use a ‘Free Hand’ in designing the composition of various parts of the webpage without getting too influenced by the existing design

Objective of the Website ‘lotstallmart.com –
a. It is a portal focussed on listing of ‘Retail’ specific real-estate properties by developers, owners and realty brokers. The properties shall listed under the following four categories-
i. Retail Malls
ii. Shopping Complexes
iii. High-street shops
iv. Retail Warehouses
*refer lotstallmart.com for better clarity

b. The abovementioned properties shall be listed either for ‘Sale’ or ‘rent\lease’ or both

c. Users shall visit the site in case they wish to acquire a retail \ shop space either on ‘sale’ or ‘rent’. These Users would be able to specify the ‘Search Criteria’ through the tool-bars provided on the website – the ‘Search Criteria’ shall comprise of ‘Type of space category’, ‘City’, ‘Locality’, transaction type ie ‘Rent \ Sale’ and ‘Area Range’

d. The main revenue model for the website shall be listing fee ( or advertising charges ) payable by those listing their properties on the website.

Three Main Pages of Website (lotstallmart.com) that need to be designed -
a. Main Home Page (visit the web link - http://lotstallmart.com/ ) - The main home page has the “Search Toolbar” for specifying of Search Criteria by the User. It shall also have the following features & functions-
i. Main Advertising Banner
ii. Featured Projects
iii. New Launches
iv. Toolbar with buttons – ‘Advertise with Us’, ‘Listings Alert’, ‘Mart Wizards’, ‘Advertiser Login’

b. Property Listings Page (visit the web link - http://lotstallmart.com/gurgaon-in-india ) - The List of property options that match the Criteria specified by the ‘User’ get displayed on this page.

c. Property Detail Page - When the ‘User’ clicks on the “More….” Button on the ‘Property Listings Page’ (given in point b. above) the web page with the details of the property opens. (For Example – visit the web link - http://lotstallmart.com/vorne-Shopping-Complex-vorne-quadrion-gurgaon-636 )

Note:- Please refer to attached ‘Shopping’ related images the designer may use them on the website to provide a look & feel of retail if required – either separately or rotate in a single window

Target Market(s)

Retailers & Investors looking for retail space, Real Estate Brokers, Developers

Industry/Entity Type

Advertising

Number of Pages Required

3 page

Requirements
Must have
• Refer to existing site lotstallmart.com -- all the existing functionalities are a must have.
Nice to have
• The Designer may use the retail related images on the website if required for making it more vibrant. Refer attached images Shopping(1-6).jpg

```html
<!DOCTYPE html>
<html lang="en">
<head>
<meta charset="utf-8">
<title>Lotstallmart.com – Retail Space Portal</title>
<link rel="stylesheet" href="https://fonts.googleapis.com/css2?family=Open+Sans:wght@400;600;700&display=swap">
<style>
:root{
  --blue:#0ea5ef;
  --blue-dark:#0a8fd4;
  --text:#333;
  --muted:#777;
  --light:#f2f2f2;
  --border:#dcdcdc;
  --topbar:#e4e4e4;
  --footer:#353535;
  --footer-bottom:#1f1f1f;
  --panel:rgba(20,20,20,.86);
  --yellow:#f5c400;
}
*{box-sizing:border-box;margin:0;padding:0}
html,body{width:1200px;height:2284px;overflow:hidden}
body{font-family:"Open Sans",Arial,sans-serif;color:var(--text);background:#fff;position:relative}
a{color:inherit;text-decoration:none}

.city-bar{height:37px;background:var(--topbar);display:flex;justify-content:center;align-items:center;font-size:12px;color:#555}
.city-bar span{padding:0 10px;border-right:1px solid #aaa;line-height:12px}
.city-bar span:last-child{border:none}

.site-header{height:138px;display:flex;align-items:center;justify-content:space-between;padding:0 119px}
.brand{display:flex;align-items:center;gap:10px}
.brand-dot{width:38px;height:38px;border-radius:50%;background:var(--blue)}
.brand-name{font-size:31px;font-weight:700;color:var(--blue);line-height:1}
.brand-tag{font-size:8.5px;font-weight:700;color:#555;margin-top:4px;letter-spacing:.2px}
.main-nav{display:flex;align-items:center}
.main-nav a{padding:0 20px;text-align:center;border-right:1px solid #ccc;color:var(--blue);font-size:15.5px;line-height:1.15}
.main-nav a small{display:block;font-size:10.5px;color:#999}
.main-nav a.active{border:1px solid #bbb;padding:6px 16px;margin-right:4px}

.account-bar{height:51px;background:var(--blue);display:flex;justify-content:center;align-items:center;gap:24px;color:#fff;font-size:12.5px}
.account-bar .login{font-weight:700;font-size:14px;display:flex;align-items:center;gap:6px}

.hero{position:relative;height:571px;background:linear-gradient(100deg,#6b2a2a 0%,#b88b70 28%,#e7d24a 40%,#c9b79a 58%,#8a8a8a 80%,#5d7b84 100%)}
.hero-arrow{position:absolute;top:267px;width:34px;height:34px;background:rgba(0,0,0,.7);display:flex;align-items:center;justify-content:center}
.hero-arrow.prev{left:0}.hero-arrow.next{right:0}
.search-panel{position:absolute;left:119px;top:21px;width:310px;height:530px;background:var(--panel);color:#fff;padding:16px 20px}
.search-panel h3{font-size:14px;font-weight:600}
.search-panel .format-link{color:var(--yellow);font-size:15px;display:block;margin-bottom:12px}
.formats{display:grid;grid-template-columns:1fr 1fr;row-gap:15px;font-size:11.5px;padding-bottom:18px;border-bottom:1px solid #555;margin:0 -20px;padding-left:20px}
.formats label{display:flex;align-items:center;gap:8px}
.formats i{width:12px;height:12px;background:#fff;display:inline-block}
.field{margin-top:18px}
.field label{font-size:12.5px;display:block;margin-bottom:10px}
.select,.keyword{height:38px;background:#fff;color:#444;font-size:12.5px;display:flex;align-items:center;justify-content:space-between;padding:0 14px}
.keyword span{color:#888}
.search-btn{display:block;margin:12px 0 0 auto;width:80px;height:36px;background:var(--blue);color:#fff;border:none;font:14px "Open Sans",sans-serif}

.formats-strip{width:962px;margin:25px auto 0;height:70px;display:flex;border-bottom:2px solid #e2e2e2}
.format-item{flex:1;display:flex;gap:10px;padding-left:4px;border-right:1px solid #ccc;height:48px}
.format-item:last-child{border:none}
.format-item svg{margin-top:4px;flex:none}
.format-item h4{font-size:19px;font-weight:600;color:var(--blue);line-height:1.1}
.format-item p{font-size:11.5px;color:#666;margin-left:2px}

.listing{width:962px;margin:6px auto 0;background:var(--light);height:308px;padding:20px 14px 0}
.listing + .listing{margin-top:12px}
.listing-head{display:flex;justify-content:space-between;align-items:center;height:40px}
.listing-head h2{font-size:26px;font-weight:600;color:var(--blue)}
.cards{display:flex;gap:14px;margin-top:10px}
.card{width:176px;height:215px;background:#fff;border:1px solid var(--border);text-align:center;padding:9px 9px 0}
.card .photo{height:112px}
.card h5{font-size:13px;font-weight:400;margin-top:17px;color:#222}
.card .city{font-size:14px;color:var(--blue);margin-top:4px}
.card .type{font-size:11.5px;color:#777;margin-top:3px}

.newsletter{position:absolute;top:1879px;left:0;width:1200px;height:80px;background:var(--blue);display:flex;align-items:center;padding:0 119px;gap:12px}
.newsletter h2{color:#fff;font-size:32px;font-weight:400;width:208px}
.nl-input{height:34px;background:#fff;font-size:14px;color:#444;display:flex;align-items:center;justify-content:space-between;padding:0 14px;width:208px}
.nl-btn{height:34px;background:#222;color:#fff;font-size:16px;width:98px;display:flex;align-items:center;justify-content:center}

.site-footer{position:absolute;top:1959px;left:0;width:1200px;height:249px;background:var(--footer);display:flex;padding:30px 119px 0;color:#aaa}
.fcol{border-right:1px solid #555;height:170px;padding-right:20px}
.fcol:last-child{border:none}
.fcol h4{color:#fff;font-size:14px;font-weight:600;margin-bottom:14px}
.fcol.about-links{width:248px}
.links{display:grid;grid-template-columns:112px 1fr;row-gap:7px;font-size:11.5px}
.fcol.about{width:248px;padding-left:20px;font-size:13px;line-height:1.6}
.fcol.contact{width:233px;padding-left:25px;font-size:13px;line-height:1.5}
.contact p{display:flex;gap:10px;margin-bottom:10px}
.fcol.wizards{padding-left:22px;width:233px}
.fbox{height:36px;background:#2a2a2a;border:1px solid #3f3f3f;margin-bottom:6px;font-size:11px;color:#888;padding:10px}
.fbtn{margin-left:auto;width:62px;height:27px;background:#666;color:#fff;font-size:12px;display:flex;align-items:center;justify-content:center}

.footer-bottom{position:absolute;top:2208px;left:0;width:1200px;height:76px;background:var(--footer-bottom);display:flex;align-items:center;justify-content:space-between;padding:0 119px;color:#aaa;font-size:12px}
.social{display:flex;gap:6px}
.social i{width:33px;height:33px;border-radius:50%;display:block}
</style>
</head>
<body>

<nav class="city-bar">
  <span>Bangalore</span><span>Chennai</span><span>Greater Noida</span><span>Gurgaon</span><span>Hyderabad</span><span>Jaipur</span><span>Khanna</span><span>Kolkatta</span><span>Mumbai</span><span>Noida</span><span>Pune</span><span>Surat</span><span>More</span>
</nav>

<header class="site-header">
  <div class="brand">
    <span class="brand-dot"></span>
    <div>
      <div class="brand-name">lotstallmart.com</div>
      <div class="brand-tag">INDIA'S LEADING PORTAL FOR RETAIL SPACE</div>
    </div>
  </div>
  <nav class="main-nav">
    <a class="active" href="#">HOME<small>Welcome</small></a>
    <a href="#">ADVERTISE WITH US<small>Standard listing - FREE</small></a>
    <a href="#">MART WIZARDS<small>Shop Search Services</small></a>
    <a href="#">LISTING ALERT<small>Newsletter Subscribe</small></a>
  </nav>
</header>

<div class="account-bar">
  <span>List your Property Here</span>
  <span class="login"><svg width="10" height="11" viewBox="0 0 10 11"><circle cx="5" cy="3" r="2.6" fill="#fff"/><path d="M0 11c0-3.5 2.2-5 5-5s5 1.5 5 5z" fill="#fff"/></svg>ADVERTISER LOGIN</span>
  <span>New Advertiser - Register</span>
</div>

<section class="hero" role="img" aria-label="Banner photo of a family shopping in front of a store window with sale signs">
  <span class="hero-arrow prev"><svg width="14" height="12" viewBox="0 0 14 12"><path d="M6 1L1 6l5 5M1 6h12" stroke="#fff" stroke-width="2.4" fill="none"/></svg></span>
  <span class="hero-arrow next"><svg width="14" height="12" viewBox="0 0 14 12"><path d="M8 1l5 5-5 5M13 6H1" stroke="#fff" stroke-width="2.4" fill="none"/></svg></span>
  <form class="search-panel">
    <h3>Select Retail Format :</h3>
    <a class="format-link" href="#">Meaning of Retail Format</a>
    <div class="formats">
      <label><i></i>Retail Mall</label><label><i></i>Shopping Complex</label>
      <label><i></i>High Street Shops</label><label><i></i>Retail Warehouses</label>
    </div>
    <div class="field"><label>Sale Or Rent Or Both :</label><div class="select">Both<svg width="12" height="7"><path d="M0 0h12L6 7z" fill="#444"/></svg></div></div>
    <div class="field"><label>Select City :</label><div class="select">Select<svg width="12" height="7"><path d="M0 0h12L6 7z" fill="#444"/></svg></div></div>
    <div class="field"><label>Select Locality/Micro-Market.</label><div class="select">Select<svg width="12" height="7"><path d="M0 0h12L6 7z" fill="#444"/></svg></div></div>
    <div class="field"><label>Enter Keyword :</label><div class="keyword"><span>Name of Project or Developet etc</span><svg width="16" height="16" viewBox="0 0 16 16"><circle cx="6.5" cy="6.5" r="5" stroke="#333" stroke-width="2" fill="none"/><path d="M10 10l5 5" stroke="#333" stroke-width="2.4"/></svg></div></div>
    <button class="search-btn" type="button">SEARCH</button>
  </form>
</section>

<section class="formats-strip">
  <div class="format-item"><svg width="24" height="24" viewBox="0 0 24 24"><circle cx="12" cy="12" r="12" fill="var(--blue)"/><path d="M6 12l4 4 8-8" stroke="#fff" stroke-width="3" fill="none"/></svg><div><h4>RETAIL MALLS</h4><p>Centrally Air-Conditioned</p></div></div>
  <div class="format-item"><svg width="24" height="24" viewBox="0 0 24 24"><circle cx="12" cy="12" r="12" fill="var(--blue)"/><path d="M6 12l4 4 8-8" stroke="#fff" stroke-width="3" fill="none"/></svg><div><h4>SHOPPING COMPLEX</h4><p>Non Air-Conditioned Building</p></div></div>
  <div class="format-item"><svg width="24" height="24" viewBox="0 0 24 24"><circle cx="12" cy="12" r="12" fill="var(--blue)"/><path d="M6 12l4 4 8-8" stroke="#fff" stroke-width="3" fill="none"/></svg><div><h4>HIGH STREET SHOPS</h4><p>Road Facing Retail</p></div></div>
  <div class="format-item"><svg width="24" height="24" viewBox="0 0 24 24"><circle cx="12" cy="12" r="12" fill="var(--blue)"/><path d="M6 12l4 4 8-8" stroke="#fff" stroke-width="3" fill="none"/></svg><div><h4>RETAIL WAREHOUSES</h4><p>Back-end Retail Storage</p></div></div>
</section>

<section class="listing">
  <div class="listing-head"><h2>FEATURED PROJECTS</h2><svg width="20" height="20" viewBox="0 0 20 20"><circle cx="10" cy="10" r="8.5" stroke="#777" stroke-width="2" fill="none"/><path d="M6 10h8M10.5 6.5L14 10l-3.5 3.5" stroke="#777" stroke-width="2" fill="none"/></svg></div>
  <div class="cards">
    <article class="card"><div class="photo" role="img" aria-label="Project building photo" style="background:linear-gradient(#c6d4e0,#a89a7c)"></div><h5>Corvale Plaza</h5><p class="city">SURAT</p><p class="type">Shopping Complex</p></article>
    <article class="card"><div class="photo" role="img" aria-label="Project building photo" style="background:linear-gradient(#23304a,#6b5a3c)"></div><h5>Corvale Plaza</h5><p class="city">SURAT</p><p class="type">Shopping Complex</p></article>
    <article class="card"><div class="photo" role="img" aria-label="Project building photo" style="background:linear-gradient(#3c8ccc,#c8d8e4)"></div><h5>Corvale Plaza</h5><p class="city">SURAT</p><p class="type">Shopping Complex</p></article>
    <article class="card"><div class="photo" role="img" aria-label="Project building photo" style="background:linear-gradient(#1d3f88,#9a7a3a)"></div><h5>Corvale Plaza</h5><p class="city">SURAT</p><p class="type">Shopping Complex</p></article>
    <article class="card"><div class="photo" role="img" aria-label="Project building photo" style="background:linear-gradient(#4a5670,#7b6a6e)"></div><h5>Corvale Plaza</h5><p class="city">SURAT</p><p class="type">Shopping Complex</p></article>
  </div>
</section>

<section class="listing">
  <div class="listing-head"><h2>NEW LAUNCHES</h2><svg width="20" height="20" viewBox="0 0 20 20"><circle cx="10" cy="10" r="8.5" stroke="#777" stroke-width="2" fill="none"/><path d="M6 10h8M10.5 6.5L14 10l-3.5 3.5" stroke="#777" stroke-width="2" fill="none"/></svg></div>
  <div class="cards">
    <article class="card"><div class="photo" role="img" aria-label="Project building photo" style="background:linear-gradient(#d8d2cc,#8a7a6a)"></div><h5>Corvale Plaza</h5><p class="city">SURAT</p><p class="type">Shopping Complex</p></article>
    <article class="card"><div class="photo" role="img" aria-label="Project building photo" style="background:linear-gradient(#2a4a7a,#5a6e8a)"></div><h5>Corvale Plaza</h5><p class="city">SURAT</p><p class="type">Shopping Complex</p></article>
    <article class="card"><div class="photo" role="img" aria-label="Project building photo" style="background:linear-gradient(#8aa4c4,#7a6e60)"></div><h5>Corvale Plaza</h5><p class="city">SURAT</p><p class="type">Shopping Complex</p></article>
    <article class="card"><div class="photo" role="img" aria-label="Project building photo" style="background:linear-gradient(#c4ccd8,#a87a7a)"></div><h5>Corvale Plaza</h5><p class="city">SURAT</p><p class="type">Shopping Complex</p></article>
    <article class="card"><div class="photo" role="img" aria-label="Project building photo" style="background:linear-gradient(#3a6a8c,#6a7a84)"></div><h5>Corvale Plaza</h5><p class="city">SURAT</p><p class="type">Shopping Complex</p></article>
  </div>
</section>

<section class="listing">
  <div class="listing-head"><h2>EDITOR'S CHOICE</h2><svg width="20" height="20" viewBox="0 0 20 20"><circle cx="10" cy="10" r="8.5" stroke="#777" stroke-width="2" fill="none"/><path d="M6 10h8M10.5 6.5L14 10l-3.5 3.5" stroke="#777" stroke-width="2" fill="none"/></svg></div>
  <div class="cards">
    <article class="card"><div class="photo" role="img" aria-label="Project building photo" style="background:linear-gradient(#5a8ac8,#c8ccd4)"></div><h5>Corvale Plaza</h5><p class="city">SURAT</p><p class="type">Shopping Complex</p></article>
    <article class="card"><div class="photo" role="img" aria-label="Project building photo" style="background:linear-gradient(#6aa0d8,#e0e4ec)"></div><h5>Corvale Plaza</h5><p class="city">SURAT</p><p class="type">Shopping Complex</p></article>
    <article class="card"><div class="photo" role="img" aria-label="Project building photo" style="background:linear-gradient(#1a1a2a,#8a3a2a)"></div><h5>Corvale Plaza</h5><p class="city">SURAT</p><p class="type">Shopping Complex</p></article>
    <article class="card"><div class="photo" role="img" aria-label="Project building photo" style="background:linear-gradient(#4a70b4,#8a8470)"></div><h5>Corvale Plaza</h5><p class="city">SURAT</p><p class="type">Shopping Complex</p></article>
    <article class="card"><div class="photo" role="img" aria-label="Project building photo" style="background:linear-gradient(#b8bcc4,#5a5a5a)"></div><h5>Corvale Plaza</h5><p class="city">SURAT</p><p class="type">Shopping Complex</p></article>
  </div>
</section>

<section class="newsletter">
  <h2>NEWS LETTER</h2>
  <div class="nl-input">Email ID</div>
  <div class="nl-input">Select Option<svg width="10" height="6"><path d="M0 0h10L5 6z" fill="#888"/></svg></div>
  <div class="nl-input">Adilabad<svg width="10" height="6"><path d="M0 0h10L5 6z" fill="#888"/></svg></div>
  <div class="nl-btn">Subscribe</div>
</section>

<footer class="site-footer">
  <div class="fcol about-links">
    <h4>About Bazaar Hub</h4>
    <div class="links">
      <span>• About Us</span><span>• Retail Malls</span>
      <span>• Privacy Policy</span><span>• Shopping Complex</span>
      <span>• Terms of Use</span><span>• High Street Shops</span>
      <span>• Contact Us</span><span>• Retail Warehouses</span>
      <span>• Site Map</span>
    </div>
  </div>
  <div class="fcol about">
    <h4>About us</h4>
    <p>Sed nec enim tempus, porta mi ut, auctor neque. Aliquam ut velit ac nibh vestibulum laoreet. Cras condimentum ut ligula eget rhoncus. In sit amet odio consequat, lobortis neque quis.</p>
  </div>
  <div class="fcol contact">
    <h4>Contact us</h4>
    <p><svg width="9" height="13" viewBox="0 0 9 13"><path d="M4.5 0A4.5 4.5 0 0 0 0 4.5C0 8 4.5 13 4.5 13S9 8 9 4.5A4.5 4.5 0 0 0 4.5 0z" fill="#aaa"/><circle cx="4.5" cy="4.5" r="1.6" fill="#353535"/></svg><span>Unit 12, 2nd Floor,<br>Block-q, Gurgaon -<br>100001</span></p>
    <p><svg width="12" height="12" viewBox="0 0 12 12"><path d="M2.5 0l2 3-1.3 1.5a7 7 0 0 0 4.3 4.3L9 7.5l3 2-1.5 2.5C5 12 0 7 0 1.5z" fill="#aaa"/></svg><span>Phone: 555 210 4471</span></p>
    <p><svg width="13" height="10" viewBox="0 0 13 10"><rect width="13" height="10" fill="#aaa"/><path d="M0 0l6.5 5L13 0" stroke="#353535" fill="none"/></svg><span>info@lotstallmart.com</span></p>
  </div>
  <div class="fcol wizards">
    <h4>Mart Wizards</h4>
    <div class="fbox">Name</div>
    <div class="fbox">E-mail</div>
    <div class="fbox">Comment</div>
    <div class="fbtn">SUBMIT</div>
  </div>
</footer>

<div class="footer-bottom">
  <span>Copyright © 2014 Lotstallmart.&nbsp;&nbsp; All rights reserved.</span>
  <div class="social">
    <i style="background:#3b5998"></i><i style="background:#1da1f2"></i><i style="background:#444"></i><i style="background:#e62117"></i><i style="background:#0e76a8"></i><i style="background:#4caf50"></i>
  </div>
</div>

</body>
</html>
```